Business Cards Design for the electrical wholesaler: clean bold dynamic :)

We need a business card design that would follow our latest brand guidelines. As an electrical wholesaler we want to bring a fresh look and feel into the industry. The design should be clean bold and dynamic. It should come alive with the renewed energy of our green colour. Our grey colour should keep things balanced and complement the notion of maturity and responsibility. We employ Lato as a corporate font however are not bound by this font and we’re open to interpretation here.

Target Market(s)

Electrical contractors

Industry/Entity Type

Business

Contact Information for Business Card

Logo
Name & Surname: Halyna Dorosh
Job Title: Director of Marketing
Email: halya.dorosh@quillmail.example
Cell phone: XXX.XXX.XXXX
Address: 20517 - 87 Ave. Edmonton, AB, Canada. T6K 4N8
Business Phone: 780.555.0184
Website: www.brovix.example

Font styles to use
Other font styles liked:
• Lato

Requirements
Must have
• Logo & website
Nice to have
• Brand elements - some of them you may find in the attached Brand Guidelines (e.g. three lines on the background signifying "W")

```html
<!DOCTYPE html>
<html lang="en">
<head>
<meta charset="utf-8">
<title>Brovix business cards</title>
<link rel="stylesheet" href="https://fonts.googleapis.com/css2?family=Exo+2:wght@500&family=Roboto:wght@400&display=swap">
<style>
  :root {
    --backdrop: #c8c8c8;
    --green: #7cb926;
    --green-deep: #5fa321;
    --green-shade: #6cad22;
    --grey: #45484b;
    --paper: #f1f1f0;
    --ink: #3d3f41;
  }
  * { margin: 0; padding: 0; box-sizing: border-box; }
  html, body { width: 1200px; height: 576px; overflow: hidden; }
  body {
    background: var(--backdrop);
    position: relative;
    font-family: "Roboto", Arial, sans-serif;
  }
  .card {
    position: absolute;
    top: 138px;
    width: 484px;
    height: 294px;
    border-radius: 12px;
    overflow: hidden;
  }
  .card--front {
    left: 82px;
    background: linear-gradient(160deg, var(--green) 0%, var(--green-shade) 60%, var(--green-deep) 100%);
  }
  .card--back {
    left: 602px;
    width: 481px;
    background: var(--paper);
  }
  .brand {
    position: absolute;
    display: flex;
    flex-direction: column;
  }
  .brand__row { display: flex; align-items: center; }
  .brand__dot {
    border-radius: 50%;
    background: var(--grey);
  }
  .brand__name {
    font-family: "Exo 2", Arial, sans-serif;
    font-weight: 500;
    color: var(--grey);
    line-height: 1;
  }
  .brand__tagline {
    text-transform: uppercase;
    color: var(--grey);
    font-family: "Roboto", Arial, sans-serif;
  }
  .card--front .brand { left: 108px; top: 112px; }
  .card--front .brand__dot { width: 40px; height: 40px; margin-right: 14px; }
  .card--front .brand__name { font-size: 56px; }
  .card--front .brand__tagline {
    font-size: 9.5px; letter-spacing: 1.6px; margin: 6px 0 0 54px; color: #3e6b14;
  }
  .card--back .brand { left: 22px; top: 22px; }
  .card--back .brand__dot { width: 24px; height: 24px; margin-right: 8px; }
  .card--back .brand__name { font-size: 32px; }
  .card--back .brand__tagline {
    font-size: 6px; letter-spacing: 0.9px; margin: 3px 0 0 32px; color: var(--green-deep);
  }
  .feature-block {
    position: absolute;
    left: 262px;
    top: 44px;
    width: 196px;
    height: 196px;
    background: var(--grey);
  }
  .contact {
    position: absolute;
    left: 22px;
    top: 124px;
    width: 230px;
    color: var(--ink);
  }
  .contact__name {
    font-family: "Exo 2", Arial, sans-serif;
    font-weight: 500;
    font-size: 21px;
    color: var(--green);
    line-height: 1.1;
  }
  .contact__title { font-size: 11.5px; margin-top: 3px; }
  .contact__address { font-size: 11.5px; line-height: 16px; margin-top: 12px; }
  .contact__list { list-style: none; margin-top: 12px; font-size: 11.5px; }
  .contact__item { display: flex; align-items: center; height: 17px; white-space: nowrap; }
  .contact__icon { width: 12px; height: 12px; margin-right: 8px; flex: none; }
</style>
</head>
<body>
  <section class="card card--front" aria-label="Card front">
    <div class="brand">
      <div class="brand__row">
        <span class="brand__dot"></span>
        <span class="brand__name">brovix</span>
      </div>
      <span class="brand__tagline">Electrical Wholesalers</span>
    </div>
  </section>

  <section class="card card--back" aria-label="Card back">
    <div class="brand">
      <div class="brand__row">
        <span class="brand__dot"></span>
        <span class="brand__name">brovix</span>
      </div>
      <span class="brand__tagline">Electrical Wholesalers</span>
    </div>

    <div class="feature-block"></div>

    <div class="contact">
      <p class="contact__name">Halyna Dorosh</p>
      <p class="contact__title">Director of Marketing</p>
      <p class="contact__address">20517 - 87 Ave. Edmonton,<br>AB, Canada T6K 4N8</p>
      <ul class="contact__list">
        <li class="contact__item">
          <svg class="contact__icon" viewBox="0 0 12 12" aria-hidden="true">
            <circle cx="6" cy="6" r="5.4" fill="none" stroke="#5fa321" stroke-width="1.1"/>
            <path d="M3.6 4.4h4.8v1H3.6zM4.2 5.6h3.6l.4 2.2H3.8z" fill="#5fa321"/>
          </svg>+1 780-555-0184
        </li>
        <li class="contact__item">
          <svg class="contact__icon" viewBox="0 0 12 12" aria-hidden="true">
            <circle cx="6" cy="6" r="5.4" fill="none" stroke="#5fa321" stroke-width="1.1"/>
            <rect x="3.4" y="4.2" width="5.2" height="3.6" fill="#5fa321"/>
            <path d="M3.4 4.2L6 6.2l2.6-2" fill="none" stroke="#f1f1f0" stroke-width=".7"/>
          </svg>halya.dorosh@quillmail.example
        </li>
        <li class="contact__item">
          <svg class="contact__icon" viewBox="0 0 12 12" aria-hidden="true">
            <circle cx="6" cy="6" r="5.4" fill="none" stroke="#5fa321" stroke-width="1.1"/>
            <circle cx="6" cy="6" r="2.8" fill="none" stroke="#5fa321" stroke-width=".9"/>
            <path d="M3.2 6h5.6M6 3.2v5.6" stroke="#5fa321" stroke-width=".7"/>
          </svg>www.brovix.example
        </li>
      </ul>
    </div>
  </section>
</body>
</html>
```